New Business Card Design Project

Use the flyer uploaded and website www.brightoakbuilders.com for inspiration.
List Our Services on Backside of business cards
Marcus Delling
Harborline Builders Inc.
Licensed General Contractors
858-471-6093

Contact Information for Business Card

Use the flyer uploaded and website www.brightoakbuilders.com for inspiration. List Our Services on Backside of business cards Marcus Delling Harborline Builders Inc. Licensed General Contractors 858-471-6093

```html
<!DOCTYPE html>
<html lang="en">
<head>
<meta charset="utf-8">
<title>Harborline Builders – Business Card</title>
<link rel="stylesheet" href="https://fonts.googleapis.com/css2?family=Cinzel:wght@400&family=Montserrat:wght@400;500;600;700&display=swap">
<style>
  :root {
    --page-bg: #e8e5df;
    --card-bg: #232325;
    --card-edge: #2e2e31;
    --text-main: #f4f4f4;
    --text-soft: #c9c9cc;
    --text-muted: #a3a3a7;
    --rule: #8a8a8e;
    --shadow: rgba(0, 0, 0, 0.35);
  }
  * { box-sizing: border-box; margin: 0; padding: 0; }
  html, body {
    width: 900px; height: 1200px; overflow: hidden;
    background: var(--page-bg);
    font-family: "Montserrat", Arial, sans-serif;
    color: var(--text-main);
  }
  .sheet {
    position: relative; width: 900px; height: 1200px;
  }
  .card {
    position: absolute; left: 60px; width: 780px; height: 450px;
    background: linear-gradient(160deg, var(--card-edge), var(--card-bg) 55%);
    border-radius: 26px;
    box-shadow: 0 14px 34px var(--shadow);
    overflow: hidden;
  }
  .card--front { top: 120px; }
  .card--back { top: 630px; }

  .brand {
    display: flex; align-items: center; gap: 14px;
    font-family: "Cinzel", Georgia, serif;
    font-weight: 400; color: var(--text-soft);
    letter-spacing: 2px; white-space: nowrap;
  }
  .brand__mark {
    width: 18px; height: 18px; background: var(--text-soft);
  }
  .card--front .brand {
    position: absolute; left: 46px; top: 48px; font-size: 32px;
  }

  .person { position: absolute; left: 46px; top: 176px; }
  .person__name { font-size: 28px; font-weight: 600; }
  .person__title { font-size: 16px; color: var(--text-soft); margin-top: 4px; }

  .divider {
    position: absolute; left: 46px; right: 46px; top: 264px;
    height: 1px; background: var(--rule);
  }

  .contacts { position: absolute; left: 46px; top: 290px; list-style: none; }
  .contacts li {
    display: flex; align-items: center; gap: 16px;
    font-size: 16px; color: var(--text-soft); height: 38px;
  }
  .contacts svg { width: 18px; height: 18px; fill: var(--text-soft); flex: none; }

  .license {
    position: absolute; right: 46px; top: 366px;
    font-size: 15px; color: var(--text-soft);
  }

  .card--back .brand {
    position: absolute; left: 0; right: 0; top: 110px;
    justify-content: center; font-size: 38px;
  }
  .services-title {
    position: absolute; left: 0; right: 0; top: 218px;
    text-align: center; font-size: 22px; font-weight: 600;
  }
  .services-rule {
    position: absolute; left: 320px; right: 320px; top: 258px;
    height: 1px; background: var(--rule);
  }
  .services {
    position: absolute; left: 20px; right: 20px; top: 284px;
    display: flex; flex-direction: column; gap: 18px;
  }
  .services__row {
    display: flex; justify-content: center; gap: 26px; list-style: none;
  }
  .services__row li {
    font-size: 14px; color: var(--text-soft); white-space: nowrap;
  }
  .services__row li::before { content: "• "; color: var(--text-main); }
</style>
</head>
<body>
<main class="sheet">

  <section class="card card--front">
    <div class="brand"><span class="brand__mark"></span>HARBORLINE BUILDERS</div>

    <div class="person">
      <p class="person__name">Marcus Delling</p>
      <p class="person__title">Managing Director</p>
    </div>

    <div class="divider"></div>

    <ul class="contacts">
      <li>
        <svg viewBox="0 0 24 24" aria-hidden="true"><path d="M6.6 10.8a15.1 15.1 0 0 0 6.6 6.6l2.2-2.2c.3-.3.7-.4 1-.2 1.1.4 2.3.6 3.6.6.6 0 1 .4 1 1V20c0 .6-.4 1-1 1A17 17 0 0 1 3 4c0-.6.4-1 1-1h3.5c.6 0 1 .4 1 1 0 1.3.2 2.5.6 3.6.1.3 0 .7-.2 1z"/></svg>
        858-471-6093
      </li>
      <li>
        <svg viewBox="0 0 24 24" aria-hidden="true"><path d="M3 5h18c.6 0 1 .4 1 1v12c0 .6-.4 1-1 1H3c-.6 0-1-.4-1-1V6c0-.6.4-1 1-1zm9 7.2L4 7.5V8l8 5 8-5v-.5z"/></svg>
        info@brightoakbuilders.com
      </li>
      <li>
        <svg viewBox="0 0 24 24" aria-hidden="true"><path d="M12 2a10 10 0 1 0 0 20 10 10 0 0 0 0-20zm6.9 6h-3a15.6 15.6 0 0 0-1.4-3.6A8 8 0 0 1 18.9 8zM12 4c.8 1.2 1.5 2.5 1.9 4h-3.8c.4-1.5 1.1-2.8 1.9-4zM4.3 14a8 8 0 0 1 0-4h3.4a16 16 0 0 0 0 4zm.8 2h3a15.6 15.6 0 0 0 1.4 3.6A8 8 0 0 1 5.1 16zm3-8h-3a8 8 0 0 1 4.4-3.6C8.9 5.6 8.4 6.8 8.1 8zM12 20c-.8-1.2-1.5-2.5-1.9-4h3.8c-.4 1.5-1.1 2.8-1.9 4zm2.3-6H9.7a14 14 0 0 1 0-4h4.6a14 14 0 0 1 0 4zm.2 5.6c.6-1.1 1.1-2.3 1.4-3.6h3a8 8 0 0 1-4.4 3.6zm1.8-5.6a16 16 0 0 0 0-4h3.4a8 8 0 0 1 0 4z"/></svg>
        www.brightoakbuilders.com
      </li>
    </ul>

    <p class="license">CSLB Licensed No. #1048826</p>
  </section>

  <section class="card card--back">
    <div class="brand"><span class="brand__mark"></span>HARBORLINE BUILDERS</div>

    <h2 class="services-title">Our Services</h2>
    <div class="services-rule"></div>

    <div class="services">
      <ul class="services__row">
        <li>Remodel: Kitchen &amp; Bath</li>
        <li>Painting: Interior &amp; Exterior</li>
        <li>Flooring: Carpet, Vinyl, Wood</li>
      </ul>
      <ul class="services__row">
        <li>Window/Door Replacement</li>
        <li>Plumbing: Repair &amp; Upgrades</li>
        <li>Energy Efficient Upgrades</li>
      </ul>
      <ul class="services__row">
        <li>Deck &amp; Patio construction</li>
        <li>Water &amp; Mold Damage</li>
        <li>Garage Renovation</li>
      </ul>
    </div>
  </section>

</main>
</body>
</html>
```